Business Card Design Project

I need a business card designed from scratch. I have an existing logo that I can upload in Illustrator for modification or redesign.

The Company is called Query Lanterns http://querylanterns.com.au and we provide Search Engine Optimization services to Australian businesses. The current logo signifies an increase in visitors, profits etc...

There are no restrictions as to the redesign - colours, style etc are all open to change.

Cards will be full colour and one sided printed at http://www.cardmoxel.com.au so check their requirements for file format and sizes etc.

I will expect all original files upon completion of project.

Target Market(s)

Any business with a web site looking to improve their search engine rankings

Industry/Entity Type

Business

Requirements
Must have
• I like modern, sleek designs. Clean, not fussy, uncluttered.

```html
<!DOCTYPE html>
<html lang="en">
<head>
<meta charset="utf-8">
<title>Query Lanterns — Business Card</title>
<link href="https://fonts.googleapis.com/css2?family=Source+Sans+3:wght@400;600;700&display=swap" rel="stylesheet">
<style>
  :root {
    --backdrop: #a97e22;
    --brand-blue: #1a73b8;
    --brand-navy: #0d3a78;
    --brand-gold: #f2b41c;
    --ink: #2a2a2a;
    --paper: #ffffff;
    --mist: #e6e6e6;
    --night: #000000;
  }
  * { margin: 0; padding: 0; box-sizing: border-box; }
  html, body { width: 1200px; height: 686px; overflow: hidden; }
  body {
    background: var(--backdrop);
    font-family: "Source Sans 3", Arial, sans-serif;
    position: relative;
  }
  .card {
    position: absolute;
    width: 463px;
    height: 265px;
    border-radius: 26px;
    overflow: hidden;
    box-shadow: 0 2px 4px rgba(0,0,0,0.35);
  }
  .card-front { left: 123px; top: 102px; background: var(--paper); }
  .card-back  { left: 605px; top: 370px; background: var(--night); }

  .front-sweep { position: absolute; inset: 0; }
  .edge-band {
    position: absolute; right: 0; top: 0; width: 22px; height: 100%;
    background: linear-gradient(to bottom, var(--brand-navy), var(--brand-blue) 55%, var(--brand-navy));
  }
  .wordmark {
    position: absolute; left: 0; width: 441px; top: 58px;
    text-align: center;
    font-weight: 700; font-size: 40px; line-height: 1;
    color: var(--brand-blue);
    letter-spacing: -0.5px;
  }
  .wordmark .mark-dot {
    display: inline-block; width: 16px; height: 16px; border-radius: 50%;
    background: var(--brand-gold); margin-right: 10px; vertical-align: 4px;
  }
  .contact {
    position: absolute; left: 0; width: 441px; top: 160px;
    text-align: center; color: var(--ink);
  }
  .contact .person { font-size: 19px; font-weight: 700; color: var(--brand-blue); line-height: 24px; }
  .contact .divider { display: inline-block; width: 1px; height: 16px; background: var(--brand-blue); margin: 0 6px; vertical-align: -2px; }
  .contact .role { font-size: 13px; font-weight: 700; color: var(--brand-gold); }
  .contact .address { font-size: 13px; line-height: 19px; }
  .contact .lines { font-size: 13px; line-height: 19px; }
  .contact .lines svg { vertical-align: -1px; margin-right: 2px; }
  .contact .lines .gap { display: inline-block; width: 12px; }
  .contact .web { font-size: 13px; font-weight: 700; color: var(--brand-blue); line-height: 19px; }
  .contact .web em { font-style: normal; color: var(--brand-gold); }

  .back-glow { position: absolute; inset: 0; }
  .back-name {
    position: absolute; left: 0; right: 0; top: 118px;
    text-align: center; font-weight: 700; font-size: 34px; color: var(--brand-gold);
  }
</style>
</head>
<body>
  <section class="card card-front">
    <svg class="front-sweep" width="463" height="265" viewBox="0 0 463 265">
      <defs>
        <linearGradient id="sweepFill" x1="0" y1="0" x2="0" y2="1">
          <stop offset="0" stop-color="#e2e2e2"/>
          <stop offset="1" stop-color="#ffffff"/>
        </linearGradient>
      </defs>
      <path d="M0 178 Q220 90 441 164 L441 265 L0 265 Z" fill="url(#sweepFill)"/>
    </svg>
    <div class="edge-band"></div>
    <div class="wordmark"><span class="mark-dot"></span>Query Lanterns</div>
    <div class="contact">
      <div class="person">Your Name<span class="divider"></span><span class="role">Title</span></div>
      <div class="address">Street name City, State, zip code</div>
      <div class="lines">
        <svg width="10" height="12" viewBox="0 0 10 12"><path d="M2 0 L4 3 L3 4.5 Q4 7.5 6 9 L7.5 8 L10 10 L8.5 12 Q2 10 0 2 Z" fill="var(--brand-blue)"/></svg>123-456-7890<span class="gap"></span>
        <svg width="13" height="9" viewBox="0 0 13 9"><rect width="13" height="9" fill="var(--brand-blue)"/><path d="M0 0 L6.5 5 L13 0" stroke="#fff" fill="none"/></svg>
        inquiry@querylanterns.com.au
      </div>
      <div class="web">www.<em>querylanterns</em>.com.au</div>
    </div>
  </section>

  <section class="card card-back">
    <svg class="back-glow" width="463" height="266" viewBox="0 0 463 266">
      <defs>
        <linearGradient id="floorFill" x1="0" y1="0" x2="0" y2="1">
          <stop offset="0" stop-color="#3a3a3a"/>
          <stop offset="1" stop-color="#0a0a0a"/>
        </linearGradient>
      </defs>
      <path d="M0 266 L0 238 Q230 140 463 238 L463 266 Z" fill="url(#floorFill)"/>
    </svg>
    <div class="back-name">Query Lanterns</div>
  </section>
</body>
</html>
```